Oversized Postcard for Estate Planning & Probate 1st 2nd and 3rd prizes

Create a professional, fresh and polished oversized post card for law firm specializing in Estate Planning & Probate Law for High Net Worth Clients

Use any picture(s) of your choice (mine or ones you recommend), logo, headshot and company info

www.morvenashbylaw.com

Westbrook Office - 4800 Kestrel Avenue, Suite 900, Millbrook, NC 27614
Harlowe Office - 13470 Birch Court, Suite 400, Millbrook, NC 27617

Phone (704) 555-0187

Use this card for a Free Consultation

Target Market(s)

young and old families too; business owners

Industry/Entity Type

Law Firm

Font styles to use
Serif
Sans Serif

Requirements
Must have
• Use any picture(s) of your choice (mine or ones you recommend), logo, headshot and company info
• www.morvenashbylaw.com
• Westbrook Office - 4800 Kestrel Avenue, Suite 900, Millbrook, NC 27614
• Harlowe Office - 13470 Birch Court, Suite 400, Millbrook, NC 27617
• Phone (704) 555-0187
• Use this card for a Free Consultation
Nice to have
• great colors and great design; like graphics with depth /shading
Should not have
• don't use too many pics - keep it simple

```html
<!DOCTYPE html>
<html lang="en">
<head>
<meta charset="utf-8">
<title>Morven Ashby Law – Estate Planning Postcard</title>
<link rel="stylesheet" href="https://fonts.googleapis.com/css2?family=Roboto+Slab:wght@300;400;500&family=Lato:wght@300;400&display=swap">
<style>
  :root {
    --teal: #1a7ba3;
    --teal-deep: #0f5a7a;
    --navy: #0b3f5a;
    --grey-text: #8a8a8a;
    --dark-text: #222;
    --button-grey: #cfcfcf;
    --white: #ffffff;
  }
  * { margin: 0; padding: 0; box-sizing: border-box; }
  html, body { width: 1200px; height: 771px; overflow: hidden; background: var(--white); }
  .postcard {
    position: relative; width: 1200px; height: 771px; overflow: hidden;
    background: var(--white);
    font-family: "Roboto Slab", Georgia, serif;
  }
  .shapes { position: absolute; inset: 0; }
  .abs { position: absolute; }

  .firm-contact { right: 196px; top: 46px; text-align: right; white-space: nowrap; }
  .firm-contact .firm-name { color: var(--teal); font-size: 22px; font-weight: 500; line-height: 1; }
  .firm-contact .line { color: var(--grey-text); font-size: 19px; font-weight: 300; line-height: 1.3; }

  .brand { left: 404px; top: 300px; width: 310px; text-align: center; }
  .brand .brand-name { color: var(--teal); font-size: 34px; font-weight: 400; line-height: 1; white-space: nowrap; }
  .brand .brand-sub { position: absolute; left: 0; top: 62px; width: 310px; text-align: center;
    font-size: 17px; color: var(--dark-text); letter-spacing: 1px; line-height: 1; }

  .schedule { left: 394px; top: 412px; width: 320px; text-align: center; }
  .schedule .lead { color: var(--teal); font-size: 19px; font-weight: 500; white-space: nowrap; }
  .schedule .phone { color: var(--grey-text); font-family: "Lato", Arial, sans-serif; font-weight: 300;
    font-size: 36px; margin-top: 2px; white-space: nowrap; }
  .schedule .phone small { font-size: 20px; font-weight: 400; }

  .office { top: 523px; width: 200px; font-size: 16px; color: var(--grey-text); line-height: 1.3; white-space: nowrap; }
  .office h3 { color: var(--teal); font-size: 21px; font-weight: 400; line-height: 1.1;
    padding-bottom: 6px; margin-bottom: 6px; border-bottom: 1.5px dotted var(--teal); display: inline-block; }
  .office-west { left: 338px; text-align: right; }
  .office-harlowe { left: 562px; text-align: left; }

  .consult { left: 406px; top: 645px; width: 330px; height: 27px; background: var(--button-grey);
    font-family: "Lato", Arial, sans-serif; font-size: 15.5px; color: var(--dark-text);
    text-align: center; line-height: 27px; }

  .attorney { left: 14px; top: 538px; width: 288px; text-align: center; }
  .attorney .name { color: var(--teal); font-size: 27px; font-weight: 400; line-height: 1.1; }
  .attorney .creds { color: var(--grey-text); font-size: 16px; font-weight: 300; padding-bottom: 8px;
    border-bottom: 1.5px dotted var(--teal); white-space: nowrap; }
  .attorney .cert { color: var(--dark-text); font-size: 15.5px; line-height: 1.25; margin-top: 9px; }

  .band-text { left: 22px; color: var(--white); font-size: 19px; font-weight: 300; line-height: 1.25; white-space: nowrap; }
  .band-practice { top: 666px; }
  .band-attorney { top: 727px; }
</style>
</head>
<body>
<div class="postcard">
  <svg class="shapes" width="1200" height="771" viewBox="0 0 1200 771">
    <defs>
      <linearGradient id="photo-tones" x1="0" y1="0" x2="1" y2="1">
        <stop offset="0" stop-color="#b9cfd6"/>
        <stop offset="0.45" stop-color="#f2dcc0"/>
        <stop offset="1" stop-color="#e0b58e"/>
      </linearGradient>
      <linearGradient id="curve-band" x1="0" y1="1" x2="1" y2="0">
        <stop offset="0" stop-color="#0b3f5a"/>
        <stop offset="1" stop-color="#1a7ba3"/>
      </linearGradient>
      <linearGradient id="headshot-tones" x1="0" y1="0" x2="0" y2="1">
        <stop offset="0" stop-color="#3a342c"/>
        <stop offset="0.5" stop-color="#c9ad86"/>
        <stop offset="1" stop-color="#d98f9a"/>
      </linearGradient>
      <linearGradient id="bottom-band" x1="0" y1="0" x2="1" y2="0">
        <stop offset="0" stop-color="#0b3f5a"/>
        <stop offset="1" stop-color="#1a82b0"/>
      </linearGradient>
    </defs>

    <path role="img" aria-label="Photo of a smiling family of four outdoors in sunlight"
          d="M0 0 H744 C640 110 520 230 320 300 C200 330 90 338 0 338 Z" fill="url(#photo-tones)"/>
    <path d="M744 0 H760 C660 130 540 250 330 308 C210 336 90 342 0 342 L0 338 C90 338 200 330 320 300 C520 230 640 110 744 0 Z"
          fill="#d8d8d8"/>
    <path d="M760 0 H800 C730 90 640 160 560 200 C470 250 400 280 330 298 C200 330 90 340 0 340 L0 342 C90 342 210 336 330 308 C540 250 660 130 760 0 Z"
          fill="url(#curve-band)"/>

    <line x1="728" y1="35" x2="1004" y2="35" stroke="#1a7ba3" stroke-width="1.5" stroke-dasharray="1.5 3"/>
    <line x1="648" y1="130" x2="1004" y2="130" stroke="#1a7ba3" stroke-width="1.5" stroke-dasharray="1.5 3"/>

    <circle cx="560" cy="226" r="67" fill="#ffffff"/>
    <circle cx="560" cy="226" r="52" fill="#1a6e93" stroke="#555" stroke-width="3"/>

    <line x1="404" y1="289" x2="714" y2="289" stroke="#222" stroke-width="1.5"/>
    <line x1="404" y1="371" x2="502" y2="371" stroke="#222" stroke-width="1.5"/>
    <line x1="616" y1="371" x2="714" y2="371" stroke="#222" stroke-width="1.5"/>

    <line x1="550" y1="524" x2="550" y2="624" stroke="#999" stroke-width="1.5"/>
    <line x1="770" y1="224" x2="770" y2="612" stroke="#333" stroke-width="1.5"/>

    <circle cx="158" cy="438" r="94" fill="#ffffff" stroke="#1a7ba3" stroke-width="2.5"/>
    <circle role="img" aria-label="Headshot of the attorney" cx="158" cy="438" r="88" fill="url(#headshot-tones)"/>

    <path d="M0 658 H268 L328 718 H0 Z" fill="#1a6e93"/>
    <path d="M0 718 H368 L416 771 H0 Z" fill="#0b3f5a"/>

    <path d="M690 746 H1200 V771 H714 Z" fill="url(#bottom-band)"/>
    <path d="M864 746 H886 L910 771 H888 Z" fill="#1a6e93" opacity="0.8"/>
    <path d="M1044 746 H1066 L1090 771 H1068 Z" fill="#2a95c2" opacity="0.8"/>
  </svg>

  <div class="abs firm-contact">
    <div class="firm-name">Morven Ashby Law, PLLC</div>
    <div class="line" style="margin-top:8px">morven@morvenashbylaw.com</div>
    <div class="line">www.morvenashbylaw.com</div>
  </div>

  <div class="abs brand">
    <div class="brand-name">Morven Ashby</div>
    <div class="brand-sub">LAW PLLC</div>
  </div>

  <div class="abs schedule">
    <div class="lead">To schedule an appointment</div>
    <div class="phone"><small>call</small> (704) 555-0187</div>
  </div>

  <div class="abs office office-west">
    <h3>Westbrook Office</h3>
    <div>4800 Kestrel Avenue,</div>
    <div>Suite 900</div>
    <div>Millbrook, NC 27614</div>
  </div>
  <div class="abs office office-harlowe">
    <h3>Harlowe Office</h3>
    <div>13470 Birch Court,</div>
    <div>Suite 400</div>
    <div>Millbrook, NC 27617</div>
  </div>

  <div class="abs consult">Use this card for a Free Consultation</div>

  <div class="abs attorney">
    <div class="name">Morven L. Ashby</div>
    <div class="creds">Attorney, CPA, LLM, CFP, MBA</div>
    <div class="cert">Board Certified Specialist in<br>Estate Planning and Probate Law</div>
  </div>

  <div class="abs band-text band-practice">Millbrook Estate Planning<br>&amp; Probate Attorneys</div>
  <div class="abs band-text band-attorney">Claire Whitford Dunn Attorney</div>
</div>
</body>
</html>
```